Velmarsh Group Webpage Design

We need a new website for our company. The company is Velmarsh Group Pty Ltd. We are in the business of Asbestos Removal; Demolition; Earthworks and Transport. We do not advertise and would like our website to be a reference point for our clients / potential clients and also to make our services known to those searching the internet for the services we offer. Some examples of the style of website we are after are:
http://www.quarnedemolition-example.com.au/
http://m.brintowerdemolitions-example.com.au/
http://www.fenwarddemolition-example.com.au
http://www.tolvik-example.com.au
http://www.ptrservices-example.com.au
http://www.steadfast-dismantling-example.com.au
We will need to work on content. Enclosed is an example. We also need to purchase the domain velmarshgroup-example.com.au and need to set up email accounts and ensure the website is mobile friendly. We have a company logo and have built our business on delivering professional, quality services on time. We would like the webpage to be simple, informative and professional - black and white / grey themed. We would also like to add a photo gallery etc later.

Industry/Entity Type

Construction

Coding

Coded - Design and coding required

Number of Pages Required

1 page

Colors
000000
fcfcfc
959595
dddddd

Requirements
Must have
• Information regarding the services we provide

```html
<!DOCTYPE html>
<html lang="en">
<head>
<meta charset="utf-8">
<title>Velmarsh Group Pty Ltd</title>
<link rel="stylesheet" href="https://fonts.googleapis.com/css2?family=Roboto:wght@300;400;500;700&family=Roboto+Condensed:wght@400;700&display=swap">
<style>
:root{
  --ink:#222;
  --muted:#6f6f6f;
  --accent:#a8504a;
  --accent-btn:#c0524b;
  --pale:#f2f2f2;
  --blog:#ececec;
  --strip:#f6f6f6;
  --footer:#6a6a6a;
  --bottom:#121212;
  --white:#fcfcfc;
  --line:#dddddd;
}
*{box-sizing:border-box;margin:0;padding:0}
html,body{width:1200px;height:2356px;overflow:hidden;background:var(--white)}
body{font-family:"Roboto",Arial,sans-serif;color:var(--ink);position:relative}
.abs{position:absolute}

/* hero */
.hero{left:0;top:0;width:1200px;height:628px;background:linear-gradient(180deg,#3c5474 0%,#647a92 40%,#7a6a52 72%,#4e3e2c 100%)}
.hero-photo{left:0;top:0;width:1200px;height:628px;background:radial-gradient(ellipse 520px 340px at 640px 330px,rgba(200,160,60,.45),transparent 70%),radial-gradient(ellipse 420px 260px at 1000px 460px,rgba(150,120,60,.35),transparent 70%)}
.logo{left:88px;top:38px;color:#fff;font-size:30px;font-weight:400;letter-spacing:4px;line-height:1}
.logo small{display:block;font-size:9px;letter-spacing:6px;text-align:center;margin-top:4px}
.menu{left:919px;top:51px;color:#fff;font-size:16px;display:flex;align-items:center;gap:9px}
.login{left:1024px;top:46px;width:86px;height:30px;border:1.5px solid #fff;border-radius:5px;color:#fff;font-size:14px;text-align:center;line-height:27px}
.hero-title{left:0;width:1200px;top:218px;text-align:center;color:#fff;font-family:"Roboto Condensed",Arial,sans-serif;font-weight:700;font-size:60px;line-height:1;text-shadow:0 2px 6px rgba(0,0,0,.4)}
.hero-sub{left:0;width:1200px;top:288px;text-align:center;color:#fff;font-weight:500;font-size:33px;text-shadow:0 2px 6px rgba(0,0,0,.4)}
.hero-btn{left:504px;top:364px;width:190px;height:50px;border:1.5px solid #fff;border-radius:5px;color:#fff;font-size:20px;text-align:center;line-height:47px;background:rgba(255,255,255,.08)}
.arrow{top:278px;width:35px;height:35px;border-radius:50%;background:rgba(30,30,30,.75)}
.arrow svg{display:block}

/* welcome */
.welcome-h{left:0;width:1200px;top:678px;text-align:center;font-size:24px;font-weight:400}
.welcome-h span{color:var(--accent)}
.welcome-p{left:94px;width:1015px;top:720px;text-align:center;font-size:12.5px;line-height:23px;color:var(--muted)}

/* services */
.services{left:0;top:833px;width:1200px;height:502px;background:var(--pale)}
.sec-h{left:0;width:1200px;text-align:center;color:var(--accent);font-size:24px;font-weight:400}
.sec-sub{left:0;width:1200px;text-align:center;font-size:16px;color:#444}
.card{top:980px;width:326px}
.card .frame{width:326px;height:200px;background:#fff;border:1px solid var(--line);padding:7px}
.card .ph{width:100%;height:100%}
.card h3{font-size:18px;font-weight:400;margin-top:25px}
.card p{font-size:11.5px;line-height:21px;color:#888;margin-top:8px}
.card a{display:block;font-size:11px;color:#222;margin-top:10px;text-decoration:none}

/* what we do */
.wwd{left:0;top:1335px;width:1200px;height:359px;background:linear-gradient(90deg,#1a1f27 0%,#232a34 55%,#3a3428 100%)}
.wwd-img{left:90px;top:1383px;width:430px;height:268px;border:3px solid #555;background:linear-gradient(160deg,#8a9aa6 0%,#b9b4a6 45%,#8c6a3e 100%)}
.wwd-h{left:545px;top:1385px;color:#fff;font-size:21px;font-weight:500}
.wwd-p{left:545px;top:1422px;width:565px;color:#eee;font-size:12.5px;line-height:21.5px;text-align:justify}
.wwd-p p+p{margin-top:20px}
.btn-red{left:545px;top:1613px;width:121px;height:34px;background:var(--accent-btn);border-radius:3px;color:#fff;font-size:12px;font-weight:500;text-align:center;line-height:34px}

/* blog */
.blog{left:0;top:1700px;width:1200px;height:264px;background:var(--blog)}
.blog-h{left:90px;top:1731px;font-size:20px;font-weight:400}
.blog-h span{color:var(--accent)}
.blog-nav{left:1090px;top:1732px}
.post-img{top:1788px;width:163px;height:132px}
.post{top:1786px;width:300px}
.post h4{font-size:14px;font-weight:500}
.post .date{color:var(--accent);font-size:13px;margin-top:10px}
.post p{font-size:11px;line-height:19px;color:#666;margin-top:6px}
.post a{display:block;color:var(--accent);font-size:12px;margin-top:7px;text-decoration:none}

/* partners */
.partners{left:0;top:1964px;width:1200px;height:99px;background:var(--strip);display:flex;justify-content:space-around;align-items:center;padding:0 90px}
.partner{color:#9a9a9a;font-size:28px;font-weight:700;font-family:"Roboto Condensed",Arial,sans-serif}

/* footer */
.footer{left:0;top:2063px;width:1200px;height:212px;background:var(--footer);color:#fff}
.fcol{top:2096px}
.fcol h5{font-size:14px;font-weight:500;margin-bottom:18px;letter-spacing:.3px}
.fcol p,.fcol li{font-size:11.5px;line-height:20px}
.email-in{width:211px;height:32px;background:#fff;border:1px solid #ccc;margin-top:12px;color:#555;font-size:11px;padding-left:10px;line-height:30px}
.sub-btn{width:96px;height:29px;background:var(--accent-btn);border-radius:3px;font-size:12px;text-align:center;line-height:29px;margin-top:12px}
.tweet{display:flex;gap:10px;margin-bottom:18px}
.tweet i{font-style:italic}
.social{display:flex;align-items:center;gap:18px;margin-bottom:10px;font-size:12px}
.social span.c{width:32px;height:32px;border:1.5px solid #ddd;border-radius:50%;display:block}
.bottom{left:0;top:2275px;width:1200px;height:81px;background:var(--bottom);color:#fff;font-size:12px;text-align:center;line-height:60px;padding-right:50px}
</style>
</head>
<body>

<header>
  <div class="abs hero"></div>
  <div class="abs hero-photo" role="img" aria-label="Photo of a yellow excavator digging at a construction site under a blue sky"></div>
  <div class="abs logo">VELMARSH<small>GROUP</small></div>
  <div class="abs menu">
    <svg width="22" height="16" viewBox="0 0 22 16"><rect y="1" width="22" height="2" fill="#fff"/><rect y="7" width="22" height="2" fill="#fff"/><rect y="13" width="22" height="2" fill="#fff"/></svg>
    MENU
  </div>
  <div class="abs login">LOGIN</div>
  <h1 class="abs hero-title">VELMARSH GROUP PTY LTD</h1>
  <div class="abs hero-sub">Neque porro quisquam est qui dolorem</div>
  <div class="abs hero-btn">VIEW MORE</div>
  <div class="abs arrow" style="left:40px"><svg width="35" height="35"><path d="M20 11l-7 6.5 7 6.5" stroke="#fff" stroke-width="2.4" fill="none"/></svg></div>
  <div class="abs arrow" style="left:1123px"><svg width="35" height="35"><path d="M15 11l7 6.5-7 6.5" stroke="#fff" stroke-width="2.4" fill="none"/></svg></div>
</header>

<section>
  <h2 class="abs welcome-h">WELCOME TO &nbsp;<span>VELMARSH GROUP PTY LTD</span></h2>
  <p class="abs welcome-p">Lorem Ipsum has been the industry's standard dummy text ever since the 1500s, when an unknown printer took a galley of type and scrambled it to make a type specimen book. It has survived not only five centuries, but also the leap into electronic typesetting, remaining essentially unchanged. It was popularised in the 1960s with the release of Typeset Co sheets containing Lorem Ipsum passages, and more recently with desktop publishing software like Pagecraft Publisher including versions of Lorem Ipsum.</p>
</section>

<section>
  <div class="abs services"></div>
  <h2 class="abs sec-h" style="top:882px">WE PROVIDE SERVICES</h2>
  <p class="abs sec-sub" style="top:924px">Lorem Ipsum is simply dummy text of the printing and typesetting industry</p>

  <div class="abs card" style="left:86px">
    <div class="frame"><div class="ph" role="img" aria-label="Photo of an excavator demolishing a building" style="background:linear-gradient(180deg,#3f78c4 0%,#8fb4dc 45%,#a09a8c 70%,#7c7262 100%)"></div></div>
    <h3>Demolition</h3>
    <p>Lorem Ipsum has been the industry's standard dummy text ever since the 1500s, when an unknown printer took a galley of type</p>
    <a>Read More &gt;&gt;</a>
  </div>
  <div class="abs card" style="left:436px">
    <div class="frame"><div class="ph" role="img" aria-label="Photo of a worker in a hard hat in front of earthmoving machinery" style="background:linear-gradient(180deg,#7fa8d4 0%,#c9b470 45%,#34437a 75%,#9a9a8a 100%)"></div></div>
    <h3>Earthworks</h3>
    <p>Lorem Ipsum has been the industry's standard dummy text ever since the 1500s, when an unknown printer took a galley of type</p>
    <a>Read More &gt;&gt;</a>
  </div>
  <div class="abs card" style="left:787px">
    <div class="frame"><div class="ph" role="img" aria-label="Photo of an asbestos removal worker in a protective suit beside a roof" style="background:linear-gradient(90deg,#3b6fb8 0%,#9aa6b0 40%,#6a7470 70%,#4c5452 100%)"></div></div>
    <h3>Asbestos</h3>
    <p>Lorem Ipsum has been the industry's standard dummy text ever since the 1500s, when an unknown printer took a galley of type</p>
    <a>Read More &gt;&gt;</a>
  </div>
</section>

<section>
  <div class="abs wwd" role="img" aria-label="Dark background photo of an excavator on a worksite"></div>
  <div class="abs wwd-img" role="img" aria-label="Photo of a worker in a protective suit carrying corrugated asbestos sheeting"></div>
  <h2 class="abs wwd-h">WHAT WE DO</h2>
  <div class="abs wwd-p">
    <p>Lorem Ipsum has been the industry's standard dummy text ever since the 1500s, when an unknown printer took a galley of type and scrambled it to make a type specimen book. It has survived not only five centuries, but also the leap into electronic typesetting, remaining essentially unchanged. It was popularised in the 1960s with the release of Typeset Co sheets containing</p>
    <p>&nbsp;It has survived not only five centuries, but also the leap into electronic typesetting, remaining essentially unchanged. It was popularised in the 1960s with the release of Typeset Co sheets containing Lorem Ipsum passages, and more recently with desktop publishing software like Pagecraft Publisher</p>
  </div>
  <div class="abs btn-red">READ MORE</div>
</section>

<section>
  <div class="abs blog"></div>
  <h2 class="abs blog-h">LATEST <span>BLOG</span></h2>
  <svg class="abs blog-nav" width="24" height="16" viewBox="0 0 24 16"><path d="M9 2L3 8l6 6M15 2l6 6-6 6" stroke="#111" stroke-width="2" fill="none"/></svg>

  <div class="abs post-img" style="left:90px;background:linear-gradient(160deg,#c9a84a 0%,#8a6a4a 50%,#5a4a3a 100%)" role="img" aria-label="Photo of an excavator among demolition rubble"></div>
  <article class="abs post" style="left:269px">
    <h4>Nemo Enim Ipsam Volup</h4>
    <div class="date">09-07-2015</div>
    <p>Lorem Ipsum has been the industry's standard dummy text ever since the 1500s, when an unknown printer took a galley of type and scrambled it to make a type specimen book.</p>
    <a>Read More &gt;&gt;</a>
  </article>

  <div class="abs post-img" style="left:624px;background:linear-gradient(90deg,#4a78b8 0%,#8a949c 50%,#5a6260 100%)" role="img" aria-label="Photo of an asbestos removal worker on a ladder"></div>
  <article class="abs post" style="left:801px">
    <h4>Nemo Enim Ipsam Volup</h4>
    <div class="date">09-07-2015</div>
    <p>Lorem Ipsum has been the industry's standard dummy text ever since the 1500s, when an unknown printer took a galley of type and scrambled it to make a type specimen book.</p>
    <a>Read More &gt;&gt;</a>
  </article>
</section>

<section class="abs partners">
  <span class="partner">Kestral</span>
  <span class="partner">Norvane</span>
  <span class="partner">Halcorp</span>
  <span class="partner">Linquor</span>
  <span class="partner">Tessa</span>
  <span class="partner">Brovik</span>
</section>

<footer>
  <div class="abs footer"></div>
  <div class="abs fcol" style="left:90px;width:240px">
    <h5>NEWSLETTERS SIGN UP</h5>
    <p style="font-size:10.5px;line-height:17px">Sign up for our daily email by entering your information below</p>
    <div class="email-in">Email address</div>
    <div class="sub-btn">SUBSCRIBE</div>
  </div>
  <div class="abs fcol" style="left:393px;width:260px">
    <h5>LATEST TWEET</h5>
    <div class="tweet"><svg width="14" height="12" viewBox="0 0 14 12"><path d="M1 10l12-8M1 2h5l7 8" stroke="#fff" stroke-width="1.4" fill="none"/></svg><p>Featured Workspace : Ironpress<br><i>vlms.to/8Rk2tQ</i>" 10 hours ago</p></div>
    <div class="tweet"><svg width="14" height="12" viewBox="0 0 14 12"><path d="M1 10l12-8M1 2h5l7 8" stroke="#fff" stroke-width="1.4" fill="none"/></svg><p>Featured Workspace : Ironpress<br><i>vlms.to/8Rk2tQ</i>" 10 hours ago</p></div>
  </div>
  <div class="abs fcol" style="left:701px;width:240px">
    <h5>GET IN TOUCH</h5>
    <p>Address : 412 Harlow Street,<br>Brenton Vale, QLD</p>
    <p style="margin-top:14px">Phone : 07 5550 1847</p>
    <p style="margin-top:14px">Email : info@velmarshgroup-example.com.au</p>
  </div>
  <div class="abs fcol" style="left:965px;width:180px">
    <h5>FOLLOW US ON</h5>
    <div class="social"><span class="c"></span>Friendloop</div>
    <div class="social"><span class="c"></span>Chirpline</div>
    <div class="social"><span class="c"></span>Snapframe</div>
  </div>
  <div class="abs bottom">Copyright © 2015.. All Rights Reserved</div>
</footer>

</body>
</html>
```